Stationery Design Project

I need a stationary design for our company. we are based in Houston, TX and we are called Mira Vell Lending. And we are wanting to brand our MoneyMendPlus program, which includes our tax preparation and restoration, credit repair service. Although our business offers other programs, we are interested in mainly focusing on The MoneyMendPlus program. We are looking for way to brand our ourselves and I believe that a great stationery design will help in achieving this goal. Our logo design is blue and light blue. the slogan is orange.

Industry/Entity Type

Business

Requirements
Must have
• Address: 30871 Calloway Ln. B-22
Houston, TX 75419
Tel. 555-318-6207
Fax 555-294-7153
www.miravelllending.example
info@miravelllending.example
Our Slogan: Happiness, Restored!

```html
<!DOCTYPE html>
<html lang="en">
<head>
<meta charset="utf-8">
<title>MoneyMendPlus Business Cards</title>
<link rel="stylesheet" href="https://fonts.googleapis.com/css2?family=Jost:wght@400;500&family=Libre+Baskerville:wght@400&display=swap">
<style>
  :root {
    --backdrop: #ece7e1;
    --card-white: #ffffff;
    --orange: #f6961f;
    --orange-light: #f9ad2c;
    --navy: #154b7c;
    --blue: #1a8ac7;
    --ink-white: #ffffff;
  }
  * { box-sizing: border-box; margin: 0; padding: 0; }
  html, body { width: 1200px; height: 723px; overflow: hidden; }
  body { background: var(--backdrop); position: relative; }

  .card {
    position: absolute;
    top: 206px;
    width: 540px;
    height: 310px;
    border-radius: 22px;
    overflow: hidden;
    box-shadow: 0 6px 18px rgba(0,0,0,0.18);
  }

  /* Front */
  .card-front { left: 40px; background: var(--card-white); }
  .front-band {
    position: absolute; left: 0; right: 0; top: 150px; bottom: 0;
    background: linear-gradient(90deg, var(--orange), var(--orange-light));
  }
  .front-stripe {
    position: absolute; left: 0; right: 0; bottom: 0; height: 50px;
    background: linear-gradient(90deg, var(--navy) 0%, var(--navy) 55%, var(--blue) 100%);
  }
  .slogan {
    position: absolute; left: 0; right: 0; bottom: 15px;
    text-align: center;
    font-family: "Libre Baskerville", Georgia, serif;
    font-size: 16px; line-height: 20px; letter-spacing: 7px;
    color: var(--orange);
  }
  .program-name {
    position: absolute; left: 44px; top: 88px;
    font-family: "Libre Baskerville", Georgia, serif;
    font-size: 38px; line-height: 46px; color: var(--navy);
    letter-spacing: -0.5px;
  }
  .partner {
    position: absolute; right: 30px; top: 30px;
    display: flex; align-items: center; gap: 10px;
  }
  .partner-square { width: 22px; height: 22px; background: var(--navy); }
  .partner-name {
    font-family: "Libre Baskerville", Georgia, serif;
    font-size: 15px; color: var(--navy);
  }
  .address {
    position: absolute; left: 40px; top: 172px; width: 210px;
    text-align: right;
    font-family: "Jost", Arial, sans-serif;
    font-size: 15px; line-height: 20px; color: var(--ink-white);
  }
  .divider {
    position: absolute; left: 266px; top: 164px; width: 1px; height: 76px;
    background: var(--ink-white);
  }
  .contacts {
    position: absolute; left: 280px; top: 160px;
    list-style: none;
    font-family: "Jost", Arial, sans-serif;
    font-size: 14.5px; line-height: 20px; color: var(--ink-white);
  }
  .contacts li { display: flex; align-items: center; gap: 7px; }
  .contacts svg { width: 11px; height: 11px; flex: none; }

  /* Back */
  .card-back {
    left: 620px;
    background: linear-gradient(135deg, var(--orange) 0%, var(--orange-light) 100%);
  }
  .back-name {
    position: absolute; left: 0; right: 0; top: 118px;
    text-align: center;
    font-family: "Libre Baskerville", Georgia, serif;
    font-size: 46px; line-height: 56px; color: var(--ink-white);
  }
  .back-url {
    position: absolute; left: 0; right: 0; top: 216px;
    text-align: center;
    font-family: "Libre Baskerville", Georgia, serif;
    font-size: 12px; letter-spacing: 3px; color: var(--ink-white);
  }
</style>
</head>
<body>

<section class="card card-front" aria-label="Business card front">
  <div class="partner">
    <span class="partner-square"></span>
    <span class="partner-name">Mira Vell Lending</span>
  </div>
  <div class="program-name">MoneyMendPlus</div>

  <div class="front-band"></div>
  <p class="address">30871 Calloway Ln. B-22<br>Houston<br>TX 75419</p>
  <div class="divider"></div>
  <ul class="contacts">
    <li>
      <svg viewBox="0 0 12 12"><path fill="#fff" d="M2.5 1 4.5 1 5.3 3.6 4 4.6a7 7 0 0 0 3.4 3.4l1-1.3L11 7.5v2A1.5 1.5 0 0 1 9.5 11 8.5 8.5 0 0 1 1 2.5 1.5 1.5 0 0 1 2.5 1z"/></svg>
      555-318-6207
    </li>
    <li>
      <svg viewBox="0 0 12 12"><path fill="#fff" d="M3 1h5v3H3zM1 5h10v5H1zM3 8h6v3H3z"/></svg>
      555-294-7153
    </li>
    <li>
      <svg viewBox="0 0 12 12"><path fill="#fff" d="M1 3h10v7H1z"/><path fill="none" stroke="#f6961f" stroke-width="1.2" d="M1 3.5 6 7l5-3.5"/></svg>
      info@miravelllending.example
    </li>
    <li>
      <svg viewBox="0 0 12 12"><circle cx="6" cy="6" r="5" fill="none" stroke="#fff" stroke-width="1.3"/><path fill="none" stroke="#fff" stroke-width="1" d="M1 6h10M6 1c-2.5 3-2.5 7 0 10M6 1c2.5 3 2.5 7 0 10"/></svg>
      www.miravelllending.example
    </li>
  </ul>

  <div class="front-stripe"></div>
  <p class="slogan">HAPPINESS, RESTORED!</p>
</section>

<section class="card card-back" aria-label="Business card back">
  <div class="back-name">MoneyMendPlus</div>
  <p class="back-url">www.miravelllending.example</p>
</section>

</body>
</html>
```